Stroll Past Linwood Infographic

Hi I need a color eye catching infographic to market my service/products to tour companies. My business card color are orange and blue. This should be a two-sided document.

```html
<!DOCTYPE html>
<html lang="en">
<head>
<meta charset="utf-8">
<title>Stroll Past Linwood Infographic</title>
<link href="https://fonts.googleapis.com/css2?family=Jost:wght@300;400;500;700&family=Open+Sans:wght@400;700&display=swap" rel="stylesheet">
<style>
:root{
  --orange:#f7941d;
  --orange-deep:#ee6a1e;
  --yellow:#ffd530;
  --blue:#137ca3;
  --ink:#231f20;
  --white:#ffffff;
  --grey:#7a7a7a;
  --quote:#f7941d;
}
*{margin:0;padding:0;box-sizing:border-box}
html,body{width:1200px;height:1000px;overflow:hidden;background:var(--white)}
body{position:relative;font-family:"Jost",sans-serif;color:var(--white)}
.section-head{position:absolute;left:222px;width:754px;height:28px;background:var(--orange);border-radius:14px 14px 0 0;color:var(--ink);font-weight:700;font-size:16px;line-height:30px;padding-left:13px}
.section-body{position:absolute;left:222px;width:754px;background:var(--blue);font-size:14.5px;line-height:19px}
.price-badge{position:absolute;width:72px;height:72px;border-radius:50%;background:radial-gradient(circle at 50% 25%,var(--yellow),var(--orange) 55%,var(--orange-deep));box-shadow:0 3px 5px rgba(0,0,0,.35);color:var(--ink);font-size:14px;line-height:17px;text-align:center;padding-top:15px;font-weight:500}
.vaudeville-body{top:78px;height:212px;padding:5px 0 0 10px;overflow:hidden}
.show-list{list-style:none}
.show-list li{position:relative;padding-left:16px}
.show-list svg{position:absolute;left:-3px;top:3px}
.show-list b{font-weight:700}
.press{margin-top:3px;text-align:center;font-size:8.5px;line-height:17px;color:var(--quote)}
.theater-body{top:363px;height:48px;text-align:center;padding:5px 4px 0;font-size:14px;line-height:18px}
.specials-arch{position:absolute;left:479px;top:425px}
.specials-title{position:absolute;left:479px;width:236px;top:458px;text-align:center;font-weight:700;font-size:18px;color:var(--white)}
.specials-body{top:487px;height:76px;text-align:center;padding:9px 10px 0}
.reviews-title{position:absolute;top:563px;left:0;width:1200px;text-align:center;color:var(--ink);font-size:22px;font-weight:300}
.review{position:absolute;top:595px;height:200px;background:var(--orange);border-radius:14px}
.review h3{text-align:center;color:var(--ink);font-family:"Open Sans",sans-serif;font-size:20px;font-weight:700;margin-top:4px}
.review p{font-size:11px;line-height:15.2px;padding:0 11px;margin-top:8px}
.review .who{position:absolute;font-size:8.5px;line-height:11px;color:var(--ink);font-family:"Open Sans",sans-serif}
.review-tail{position:absolute;top:792px}
.review-left{left:228px;width:366px}
.review-right{left:604px;width:367px}
.story{position:absolute;top:814px;left:236px;width:728px;text-align:center;color:var(--grey);font-size:14.6px;line-height:17px;font-weight:300;letter-spacing:.15px}
.contact-btn{position:absolute;left:517px;top:871px;width:182px;height:42px;border-radius:21px;background:linear-gradient(var(--yellow),var(--orange) 45%,var(--orange-deep));box-shadow:0 2px 3px rgba(0,0,0,.3);text-align:center;font-weight:700;font-size:24px;line-height:42px;color:var(--ink);z-index:2}
.footer{position:absolute;left:213px;top:908px;width:772px;height:47px;background:var(--blue);text-align:center;font-size:14.5px;line-height:19px;padding-top:5px}
.fine-print{position:absolute;top:958px;left:0;width:1200px;text-align:center;color:var(--grey);font-size:13.5px;line-height:17px}
</style>
</head>
<body>

<div class="section-head" style="top:50px">Vaudeville - No one does it better than Cabaret Marigold</div>
<div class="price-badge" style="left:892px;top:12px">Starting<br>at $50</div>
<div class="section-body vaudeville-body">
  <p>For over 20 years, Cabaret Marigold has worked with performing artists from Broadway Theater, television, film and recording to bring vaudeville to YOU.&nbsp; Where else you can get a live show and dinner starting at $50?</p>
  <p>Here's a taste of just a few of our breathtaking shows</p>
  <ul class="show-list">
    <li><svg width="14" height="14" viewBox="0 0 14 14"><circle cx="7" cy="7" r="6.5" fill="#fff"/><path d="M3.8 7.2l2.2 2.2 4.2-4.6" stroke="#231f20" stroke-width="1.8" fill="none"/></svg><b>Parlor Rhythm Revue</b> – A musical tribute to Pearl Dawson, Louis Harlan, Etta Morrow, Ray Whitfield and others</li>
    <li><svg width="14" height="14" viewBox="0 0 14 14"><circle cx="7" cy="7" r="6.5" fill="#fff"/><path d="M3.8 7.2l2.2 2.2 4.2-4.6" stroke="#231f20" stroke-width="1.8" fill="none"/></svg><b>Velvet Lamplight Voices</b> – Featuring the music of Ella Brightwater, Louis Carver, Joe Winslow &amp; Dinah Castell</li>
    <li><svg width="14" height="14" viewBox="0 0 14 14"><circle cx="7" cy="7" r="6.5" fill="#fff"/><path d="M3.8 7.2l2.2 2.2 4.2-4.6" stroke="#231f20" stroke-width="1.8" fill="none"/></svg><b>Moonlit Melodies</b> – Featuring the music of Cole Bramley</li>
    <li><svg width="14" height="14" viewBox="0 0 14 14"><circle cx="7" cy="7" r="6.5" fill="#fff"/><path d="M3.8 7.2l2.2 2.2 4.2-4.6" stroke="#231f20" stroke-width="1.8" fill="none"/></svg><b>Three Gentlemen of Swing</b> – Featuring the music of Duke Ashford, Count Radley &amp; Nat Kingsley</li>
    <li><svg width="14" height="14" viewBox="0 0 14 14"><circle cx="7" cy="7" r="6.5" fill="#fff"/><path d="M3.8 7.2l2.2 2.2 4.2-4.6" stroke="#231f20" stroke-width="1.8" fill="none"/></svg><b>The Songbird Trio of jazz</b> – Featuring the music of Ella Brightwater, Billie Holloway and Dinah Castell.</li>
  </ul>
  <div class="press">
    "A Treat, It's Fresh &amp; Bouncy &amp; Loads of Fun" – City Visitor Guide<br>
    "A Marigold of a Show.....Something For Everyone." – Metro Evening Post<br>
    "A Smorgasbord of Talent.&nbsp; The Perfect Show for Visitors to Our City to Enjoy." - Curtain Call Magazine
  </div>
</div>

<div class="section-head" style="top:335px">Theater – Riveting, not to be missed, and one of a kind</div>
<div class="price-badge" style="left:892px;top:298px">Starting<br>at $25</div>
<div class="section-body theater-body"><b>Iron Street, The Lantern, The Gathering</b> and so much more.&nbsp; Tickets start at $25, and we can arrange to have<br>dinner included for your group.</div>

<svg class="specials-arch" width="236" height="64" viewBox="0 0 236 64">
  <path d="M0 64 A118 62 0 0 1 236 64 Z" fill="#f7941d"/>
  <path d="M43 64 A75 36 0 0 1 193 64 Z" fill="#231f20"/>
</svg>
<div class="specials-title">Specials</div>
<div class="section-body specials-body">There are amazing not-to-be-missed shows that happen only once a year –sometimes even less frequently– and only those “in the know” get to experience them. Check in with us often to see what's going on in Harlem and you'll never miss another house tour, Christmas Day concert or dance celebration.</div>

<div class="reviews-title">See what our customers are saying about us!</div>

<div class="review review-left">
  <h3>Great way to end our NYC trip !!!</h3>
  <p>Our Harlem bus tour was the perfect ending to a 3-day group trip to NYC. Marjorie was very accommodating and responsive during the planning of the custom tour and lunch. The tour was everything we discussed and more. The group loved the tour and the combination of the tour stops was a great way for a group with ages ranging from 6 to 70 years to cover a lot of ground in 5 hours. We truly learned about Harlem - past, present, and future. Stroll Past Linwood will definitely be my choice for all future Harlem tours!!!</p>
  <div class="who" style="left:289px;top:162px">Denise R.<br>Emporia, VA<br>07/22/2014</div>
</div>
<svg class="review-tail" style="left:530px" width="46" height="20" viewBox="0 0 46 20"><path d="M0 0 L46 20 L30 0 Z" fill="#f7941d"/></svg>

<div class="review review-right">
  <h3>Spring in Harlem !!!</h3>
  <p>If you want to feel good about life, go to Harlem in May, befriend Beatrice, and go sing in Church on a Sunday. This tour was so fun. I learned a ton about the history of NYC and Harlem. It's all there: Adam Whitcombe, churches and mosques, Marco the artist, the Starlight theater, 125th St , Lenox Ave, lovely people in church and on the streets, the parks, and the food. Don't miss it.<br>(this is the best Ambassador that I have ever met)</p>
  <div class="who" style="left:289px;top:162px">LakeviewTraveler<br>California<br>05/14/2014</div>
</div>
<svg class="review-tail" style="left:906px" width="46" height="20" viewBox="0 0 46 20"><path d="M0 0 L46 20 L30 0 Z" fill="#f7941d"/></svg>

<p class="story">Harlem has so much more to offer than gospel (although, the area's gospel choirs are second-to-none). Since the<br>1650s when Harlem (Nieuw Haarlem) was incorporated under Pieter Vandermeer, this north Manhattan community<br>had an identity all to its own. Now, it's time for YOU to discover why Harlem is so sizzling HOT!</p>

<div class="contact-btn">Contact us!</div>

<div class="footer">Stroll Past Linwood |1480 Linwood Avenue, Suite D| New York, NY 10027 | Tel: (212) 555-0147 |<br>Fax: (646) 555-0193 | Email: info@strollpastlinwood.com |www.strollpastlinwood.com</div>

<p class="fine-print">There is still time to participate in some of our upcoming events<br>Prices expire on December 31, 2015</p>

</body>
</html>
```